Dashboard Elements

Hello – looking for someone to create dashboard elements.
I’ve already basically designed all these elements – but I need someone to take what I’ve designed and make it look like an actual dashboard UI, like an app - assuming using some kind of dashboard UI kit (but however you would like to get it done is fine). It can look just like mine or try something different, as long as it matches the color scheme webpage that I’m going to out it on – see the page here. I’m ok with making it dark, maybe that would look better – again as long as it matches the webpage (https://www.plandeck.io/file/7QxKtr2BwLpZnVe4Hs8Mc1/Webpage-with-placeholders?node-id=0%3A1). Please note, you do not need to put anything on the webpage or do anything with this Plandeck file, this is just a reference so you can color/stylize it accordingly.

The attached Powerpoint file has everything you need - make sure to zoom all the way out to see everything on the slides.

Here are the Dashboard elements needed (this will all make sense when you look at the PPT):
Dashboard 1
Dashboard 1 – expanded view A
Dashboard 1 – expanded view B
View Source button by itself
Source Document Viewer 1 and 2 (these are exactly the same just with a different image inside)*
Dashboard 2 (only slightly different than Dashboard 1, just extended with extra headings
Table of Contents
Searchbar and Source Doc by itself
*the documents in the source document viewers should still look like documents - they don’t need to look like part of the UI, because this is a document viewer – you can restyle/recolor if necessary or just leave these as is.
- Colors must match color scheme of webpage, attached and on Plandeck link (images there currently are only placeholders) – ok to go dark as long as it matches
- Must look sleek, clean, realistic
- Don’t add any pictures of people or change the text.
- In case it’s not clear, this is what I mean by the concept of Dashboard UI - https://www.notavia.net/shard/s7/sh/8fad21bc-14e9-4a7c-b2d0-5c3e9f71a604/92c4e1b7a05d3f68e1c2b947d0a3f815
- Must be sent in an editable file, I may need to be edit text and other elements
- If you are going to send a sample, please make sure it’s part of the dashboard itself, not just the table of contents etc

Ideally hoping to find someone I can continue working with as I'll have a lot more graphic design work needed coming up.

Thank you!

```html
<!DOCTYPE html>
<html lang="en">
<head>
<meta charset="utf-8">
<title>Source Document Viewer Fax &amp; Lab</title>
<link rel="stylesheet" href="https://fonts.googleapis.com/css2?family=Poppins:wght@400;500;600;700&family=PT+Sans:wght@400;700&display=swap">
<style>
:root{
  --bg:#120f28;
  --panel:#1c1946;
  --content:#23205a;
  --field:#2d2a6b;
  --purple:#7d6cf2;
  --purple-2:#8a63e6;
  --teal:#2fc3c6;
  --teal-2:#29a8b5;
  --blue:#2b76d8;
  --white:#ffffff;
  --muted:#c9c6e8;
  --line:#e9e7f7;
  --danger:#f0445a;
}
*{box-sizing:border-box;margin:0;padding:0}
html,body{width:1200px;height:3181px;overflow:hidden}
body{
  position:relative;
  font-family:"Poppins",sans-serif;color:var(--white);
  background:
    radial-gradient(420px 300px at 0 40px,rgba(47,195,198,.35),transparent 70%),
    radial-gradient(380px 500px at 1200px 900px,rgba(47,195,198,.22),transparent 70%),
    radial-gradient(340px 340px at 1200px 2050px,rgba(125,108,242,.35),transparent 70%),
    var(--bg);
}
.abs{position:absolute}
.sheet-title{position:absolute;top:44px;left:0;width:1200px;text-align:center;color:var(--purple);font-weight:600;font-size:35px;line-height:42px}
.sheet-title .accent{color:#4fb0f2}

/* dashboard */
.dashboard{position:absolute;left:31px;top:170px;width:1138px;height:1383px;background:var(--panel)}
.brand-mark{left:48px;top:34px;width:36px;height:36px;border-radius:50%;background:var(--teal)}
.brand-name{left:122px;top:26px;font-size:23px;font-weight:600;color:#52b4e6}
.brand-tag{left:122px;top:62px;font-size:10px;font-weight:500;letter-spacing:.2px}
.top-grid{left:880px;top:42px}
.notify{left:933px;top:40px;width:38px;height:22px;border-radius:11px;background:var(--teal-2);font-size:9px;text-align:center;line-height:22px;font-weight:600}
.avatar{left:991px;top:39px;width:22px;height:22px;border-radius:4px;background:linear-gradient(135deg,#c9a98d,#6b4d3c)}
.user{left:1022px;top:42px;font-size:11px}
.sidebar-label{left:34px;font-size:14px;font-weight:500}
.nav-item{left:34px;height:34px;display:flex;align-items:center;font-size:14px}
.nav-icon{width:34px;height:34px;border-radius:5px;background:#2a275f;display:flex;align-items:center;justify-content:center;margin-right:8px}
.nav-item.active{color:var(--teal)}
.content{left:218px;top:95px;width:920px;height:1226px;background:var(--content)}
.footer-copy{left:247px;top:1344px;font-size:13px;font-weight:500}
.footer-brand{right:36px;top:1344px;font-size:13px;color:#52b4e6}

.icon-btn{width:33px;height:33px;border-radius:5px;background:#3a3785;display:flex;align-items:center;justify-content:center}
.crumb{font-size:18px;font-weight:600}
.crumb .link{color:var(--teal);font-weight:500}
.mini-search{left:830px;top:113px;width:272px;height:33px;border-radius:5px;background:var(--field);display:flex;align-items:center;padding:0 4px 0 12px;font-size:11px;color:var(--muted)}
.mini-search .sel{margin-left:auto;color:var(--teal);font-size:10px;border-left:1px solid var(--teal);padding-left:5px;margin-right:8px}
.mini-search .go{width:24px;height:24px;border-radius:4px;background:var(--teal);display:flex;align-items:center;justify-content:center}
.profile{left:247px;top:173px;font-size:15px}
.profile b{color:var(--teal);font-weight:500;margin-right:8px}
.updated{right:36px;top:173px;font-size:15px}
.updated span{color:var(--teal)}
.stat{top:208px;width:142px;height:52px;border-radius:5px;padding:9px 16px;font-size:10px;line-height:15px}
.stat strong{display:block;font-size:13px;font-weight:600;letter-spacing:1px}
.stat .dot{position:absolute;right:16px;top:10px;width:32px;height:32px;border-radius:50%;background:#1f2050}
.stat.raf{left:247px;background:var(--blue)}
.stat.cond{left:413px;background:var(--teal-2)}
.stat.idn{left:581px;background:var(--purple-2)}
.hcc{left:247px;top:290px;font-size:17px;font-weight:600}
.hcc .link{color:var(--teal);font-weight:500}
.docname{left:247px;top:330px;font-size:13px;font-weight:600}
.close-doc{right:36px;top:322px;display:flex;align-items:center;font-size:13px;font-weight:600}
.close-doc .x{width:31px;height:31px;border-radius:4px;background:#3a3785;margin-left:10px;display:flex;align-items:center;justify-content:center}

/* document */
.doc{left:247px;top:371px;width:855px;height:926px;background:#fff;color:#111;font-family:"PT Sans",sans-serif}
.doc-title{left:127px;top:62px;font-family:"Poppins",sans-serif;font-weight:700;font-size:22px}
.doc-rule{left:127px;top:96px;width:548px;height:2px;background:#222}
.doc-rule.top{top:60px;height:1px}
.trust{left:690px;top:60px;width:40px;text-align:center;font-weight:700;font-size:11px}
.trust i{display:block;width:32px;height:16px;margin:3px auto 0;background:#ddd}
.id-box{left:127px;top:113px;width:297px;height:121px;border:1.5px solid #222;font-size:11.5px;padding:2px 4px;line-height:15px}
.id-box .stamp{position:absolute;left:110px;top:20px;color:#d8d8d8;font-weight:700;font-size:21px;text-align:center;line-height:25px}
.admit{font-size:12px;line-height:20px}
.doc-body{left:127px;top:243px;width:605px;font-size:11.5px;line-height:15.2px}
.doc-body h4{font-family:"Poppins",sans-serif;font-size:13.5px;margin-bottom:3px}
.doc-body p{margin-bottom:9px}
.doc-body ul{margin:-8px 0 9px 66px;list-style:disc}
.score{left:202px;width:441px;border:1.5px solid #222;padding:4px 22px;font-size:10px;line-height:13.6px}
.score h5{font-size:12px;margin-bottom:1px}

/* components */
.h2{position:absolute;color:var(--purple);font-weight:600;font-size:35px}
.toc{position:absolute;left:31px;width:399px;height:69px;border-radius:5px;background:var(--panel);display:flex;align-items:center;padding:0 0 0 34px;font-size:21px;font-weight:600}
.toc .toggle{margin-left:auto;margin-right:12px;width:46px;height:46px;border-radius:6px;display:flex;align-items:center;justify-content:center}
.page-search{position:absolute;left:545px;top:1710px;width:624px;height:80px;border-radius:7px;background:var(--field);display:flex;align-items:center;padding:0 12px 0 28px;font-size:29px}
.page-search .sel{margin-left:30px;border-left:2px solid var(--teal);padding-left:12px;color:var(--teal);font-size:27px;display:flex;align-items:center;gap:12px}
.go-lg{margin-left:auto;width:54px;height:54px;border-radius:8px;background:var(--teal);display:flex;align-items:center;justify-content:center}
.table-search{position:absolute;left:545px;top:1927px;width:408px;height:77px;border-radius:7px;background:var(--field);display:flex;align-items:center;padding:0 13px 0 42px;font-size:28px}
.toc-list{position:absolute;left:31px;top:2006px;width:399px;height:1090px;border:2px solid #2d2a6b;border-radius:4px;background:var(--panel);padding:0 30px}
.toc-item{position:absolute;left:31px;width:337px;font-size:26px;font-weight:500;border-bottom:2px solid var(--line);padding-bottom:18px}
.toc-item.active{color:var(--teal);border-color:var(--teal)}
</style>
</head>
<body>

<h1 class="sheet-title">Source Document Viewer Fax &amp; Lab<br>Created with <span class="accent">Plandeck</span></h1>

<section class="dashboard">
  <div class="abs brand-mark"></div>
  <div class="abs brand-name">MedArcis</div>
  <div class="abs brand-tag">EACH PATIENTS' FULL MEDICAL HISTORY, SUMMARY AND ANALYSIS IN ONE COMPREHENSIVE HEALTH RECORD</div>
  <svg class="abs top-grid" width="18" height="18" viewBox="0 0 18 18" fill="#7d6cf2"><circle cx="3" cy="3" r="1.6"/><circle cx="9" cy="3" r="1.6"/><circle cx="15" cy="3" r="1.6"/><circle cx="3" cy="9" r="1.6"/><circle cx="9" cy="9" r="1.6"/><circle cx="15" cy="9" r="1.6"/><circle cx="3" cy="15" r="1.6"/><circle cx="9" cy="15" r="1.6"/><circle cx="15" cy="15" r="1.6"/></svg>
  <div class="abs notify">&#9650; 27</div>
  <div class="abs avatar" role="img" aria-label="User profile photo"></div>
  <div class="abs user">Dana Admin &#9662;</div>

  <nav>
    <div class="abs sidebar-label" style="top:114px">Main</div>
    <div class="abs nav-item" style="top:143px"><span class="nav-icon"><svg width="14" height="14" fill="#fff"><rect width="6" height="8"/><rect x="8" width="6" height="5"/><rect y="10" width="6" height="4"/><rect x="8" y="7" width="6" height="7"/></svg></span>Dashboard</div>
    <div class="abs nav-item" style="top:186px"><span class="nav-icon"><svg width="16" height="14" fill="#fff"><circle cx="5" cy="4" r="3"/><circle cx="11" cy="4" r="2.5"/><path d="M0 13a5 5 0 0 1 10 0zM9 13a4 4 0 0 1 7 0z"/></svg></span>Employee</div>
    <div class="abs nav-item" style="top:230px"><span class="nav-icon"><svg width="12" height="14" fill="#fff"><path d="M0 0h8l4 4v10H0z"/></svg></span>Document</div>
    <div class="abs nav-item" style="top:273px"><span class="nav-icon"><svg width="14" height="14" fill="#fff"><rect y="2" width="14" height="12" rx="1"/><rect x="3" width="2" height="4"/><rect x="9" width="2" height="4"/></svg></span>Appointment</div>
    <div class="abs nav-item" style="top:316px"><span class="nav-icon"><svg width="14" height="14" fill="#fff"><path d="M1 3l9 4-2 3-8-4zM6 9v5h2"/></svg></span>Surveillance</div>
    <div class="abs nav-item active" style="top:360px"><span class="nav-icon"><svg width="14" height="14" fill="#2fc3c6"><rect width="6" height="6"/><rect x="8" width="6" height="6"/><rect y="8" width="6" height="6"/><rect x="8" y="8" width="6" height="6"/></svg></span>Reports</div>
    <div class="abs sidebar-label" style="top:424px">Support</div>
    <div class="abs nav-item" style="top:453px"><span class="nav-icon"><svg width="14" height="14"><circle cx="7" cy="7" r="6" fill="#fff"/><circle cx="7" cy="7" r="2.2" fill="#2a275f"/></svg></span>Settings</div>
    <div class="abs nav-item" style="top:496px"><span class="nav-icon"><svg width="14" height="14"><circle cx="7" cy="7" r="7" fill="#fff"/><text x="7" y="11" font-size="10" font-weight="700" text-anchor="middle" fill="#2a275f">?</text></svg></span>Tutorial</div>
  </nav>

  <main class="abs content"></main>

  <div class="abs icon-btn" style="left:247px;top:113px"><svg width="14" height="14" fill="#2fc3c6"><rect width="6" height="6"/><rect x="8" width="6" height="6"/><rect y="8" width="6" height="6"/><rect x="8" y="8" width="6" height="6"/></svg></div>
  <div class="abs crumb" style="left:291px;top:116px"><span class="link">Reports</span> &#9656; C-CDA Compendium</div>
  <div class="abs icon-btn" style="left:780px;top:113px"><svg width="14" height="13" fill="#2fc3c6"><rect x="3" width="8" height="4"/><rect y="4" width="14" height="6" rx="1"/><rect x="3" y="8" width="8" height="5"/></svg></div>
  <div class="abs mini-search">Type ID Number here<span class="sel">ID Number &#9662;</span><span class="go"><svg width="13" height="13" fill="none" stroke="#fff" stroke-width="2"><circle cx="6" cy="6" r="4.5"/><path d="M9.5 9.5l3 3"/></svg></span></div>

  <div class="abs profile"><b>Patient Profile</b>Lena Moss | Female | 70 Years Old | 01-11-1951</div>
  <div class="abs updated"><span>Last Updated:</span> May 24, 2021</div>

  <div class="abs stat raf">R A F<strong>1 . 4 6 2</strong><span class="dot"></span></div>
  <div class="abs stat cond">Condition<strong>5</strong><span class="dot"></span></div>
  <div class="abs stat idn">ID Number<strong>7326472</strong><span class="dot"></span></div>

  <div class="abs hcc"><span class="link">&#9662; HCC Summary</span> &#9656; Documents</div>
  <div class="abs docname">Document Name Here</div>
  <div class="abs close-doc">Close Document<span class="x"><svg width="14" height="14" stroke="#f0445a" stroke-width="2.5"><path d="M1 1l12 12M13 1L1 13"/></svg></span></div>

  <article class="abs doc">
    <div class="abs doc-rule top"></div>
    <div class="abs doc-title">Patient Observation Chart</div>
    <div class="abs doc-rule"></div>
    <div class="abs trust">CTR<i></i></div>
    <div class="abs id-box">Name<br>Address<br><br><br><br>Hospital No.<br>DOB<div class="stamp">AFFIX<br>PATIENT<br>ID</div></div>
    <div class="abs admit" style="left:458px;top:127px">Admitted<br>Transferred<br>Transferred</div>
    <div class="abs admit" style="left:558px;top:127px">Date_______<br>Date_______<br>Date_______</div>
    <div class="abs admit" style="left:658px;top:127px">Ward_____<br>Ward_____<br>Ward_____</div>

    <div class="abs doc-body">
      <h4>Patient Observation Chart Guidelines</h4>
      <p>Not all patients will require every part of this observation chart to be completed. Clinical judgement should be used to dictate the type and frequency of vital sign monitoring required.</p>
      <p>The following patients are considered to be at high risk of developing a critical illness therefore it would be considered good practice to commence MEWS at the earliest opportunity.</p>
      <ul><li>All emergency admissions</li><li>Unstable patients</li><li>Patients whose condition is causing concern</li><li>Patients requiring frequent or increasing frequency of observations</li><li>Patients who have stepped down from a higher level of care</li><li>Patients with a chronic health problem</li><li>Patients who are failing to progress</li><li>Post-operative patients</li></ul>
      <p>There are also patients in whom the use of MEWS may be inappropriate:</p>
      <ul><li>Day case patients</li><li>Patients requiring no observations</li><li>Patients who are terminally ill</li><li>Planned discharges.</li></ul>
      <p>This is not an exhaustive list. Although the majority of patients may benefit from utilisation of the scoring system, a nurse's own clinical judgement dictates whether the he/she feels the patient requires scoring. For guidance on the use of MEWS, refer to the Nurse in Charge.</p>
    </div>

    <div class="abs score" style="top:613px;height:139px">
      <h5>Pain Score</h5>
      Remember to check scores after pain relief.<br>Patient asked to report pain at rest and on movement.<br>0 = No pain at rest or on movement<br>1 = No pain at rest, slight pain on movement<br>2 = Intermittent pain at rest, moderate on movement<br>3 = Continuous pain at rest severe on movement<br>Review 5 mins after I/V, 1 hour after I/M, S/C or oral analgesia.<br>Sustained pain score of 2 or pain score of 3 requires intervention.
    </div>
    <div class="abs score" style="top:759px;height:114px">
      <h5>Sedation Score</h5>
      0 = Awake, alert, orientated<br>1 = Mild, aroused by verbal stimulus<br>2 = Moderate, aroused by physical stimulus<br>3 = Severe, no response<br>S = Normal sleep, easy to rouse<br>Score 2 or 3 requires immediate intervention
    </div>
  </article>

  <div class="abs footer-copy">&copy; 2021 - All Rights Licensed</div>
  <div class="abs footer-brand">MedArcis</div>
</section>

<h2 class="h2" style="left:31px;top:1622px">Table of Content</h2>
<h2 class="h2" style="left:545px;top:1622px">Search Bar Page</h2>

<div class="toc" style="top:1716px">Table of Contents<span class="toggle" style="background:var(--teal-2)"><svg width="16" height="10" fill="#fff"><path d="M0 0h16L8 9z"/></svg></span></div>

<div class="page-search">Type ID Number here<span class="sel">ID Number <svg width="18" height="10" fill="#2fc3c6"><path d="M0 0h18L9 9z"/></svg></span><span class="go-lg"><svg width="28" height="28" fill="none" stroke="#fff" stroke-width="3"><circle cx="12" cy="12" r="9"/><path d="M19 19l6 6"/></svg></span></div>

<h2 class="h2" style="left:31px;top:1834px">Table of Content - Expand</h2>
<h2 class="h2" style="left:545px;top:1834px">Search Bar Table &amp; Document</h2>

<div class="toc" style="top:1927px">Table of Contents<span class="toggle" style="background:var(--purple)"><svg width="16" height="10" fill="#fff"><path d="M0 10h16L8 1z"/></svg></span></div>

<div class="table-search">Search<span class="go-lg" style="width:58px;height:58px"><svg width="28" height="28" fill="none" stroke="#fff" stroke-width="3"><circle cx="12" cy="12" r="9"/><path d="M19 19l6 6"/></svg></span></div>

<div class="toc-list"></div>
<div class="toc-item active" style="top:2034px">Insurance Providers</div>
<div class="toc-item" style="top:2113px">Problem</div>
<div class="toc-item" style="top:2206px">Results</div>
<div class="toc-item" style="top:2308px">Procedures</div>
<div class="toc-item" style="top:2411px">Encounters</div>
<div class="toc-item" style="top:2513px">Medications</div>
<div class="toc-item" style="top:2616px">Vital Signs</div>
<div class="toc-item" style="top:2718px">Immunizations</div>
<div class="toc-item" style="top:2821px">Social History</div>
<div class="toc-item" style="top:2923px">Family History</div>
<div class="toc-item" style="top:3026px;border-bottom:none">Plan of Care</div>

</body>
</html>
```